We need a business card design for a new company located in Brampton Ontario Canada. Our goal is to promote companies to use our service as an "External Program Management " firm taking their industrial product concepts " from prototype to production." We would like to use blue and yellow as our colors. Our skills include finding suppliers for prototype parts and developing them into supplying not only prototypes but the final production parts as well for our customer base.
Industry/Entity Type
Business
Contact Information for Business Card
Derek Namsby
Sales Manager
KOLVEN Solutions Inc.
14 Pinemarsh Lane
Brampton, Ontario L7P 2K9
Canada
Phone: 905-481-2976
Fax: 905-481-2976
website: www.kolvensolutions-example.com
Email: derek@kolvensolutions-example.com
Look and feel
Each slider illustrates characteristics of the customer's brand and the style your logo design should communicate.

```html
<!DOCTYPE html>
<html lang="en">
<head>
<meta charset="utf-8">
<title>KOLVEN Solutions Inc. – Business Card</title>
<link rel="stylesheet" href="https://fonts.googleapis.com/css2?family=Exo+2:wght@400;500;700&display=swap">
<style>
  :root {
    --card-blue: #123a6b;
    --accent-yellow: #f7c51e;
    --line-white: #ffffff;
    --ink-dark: #10233f;
    --page-bg: #e9e7e3;
    --edge-blue: #0b2748;
  }
  * { margin: 0; padding: 0; box-sizing: border-box; }
  html, body {
    width: 1200px; height: 1050px; overflow: hidden;
    background: var(--page-bg);
    font-family: "Exo 2", Verdana, sans-serif;
  }
  .canvas { position: relative; width: 1200px; height: 1050px; }

  .card {
    position: absolute; top: 157px;
    width: 420px; height: 735px;
    background: var(--card-blue);
    overflow: hidden;
    box-shadow: 0 10px 30px rgba(0,0,0,.25);
  }
  .card--front { left: 150px; }
  .card--back  { left: 630px; }

  /* Front */
  .top-rule { position: absolute; left: 0; right: 0; background: var(--line-white); }
  .top-rule--thin  { top: 28px; height: 2px; }
  .top-rule--thick { top: 40px; height: 4px; }
  .logo-rule { position: absolute; left: 0; right: 0; top: 168px; height: 3px; background: var(--line-white); }

  .brand {
    position: absolute; top: 70px; left: 0; right: 0;
    text-align: center; color: var(--accent-yellow);
    font-weight: 700; line-height: 1;
  }
  .brand__name { font-size: 54px; letter-spacing: 2px; }
  .brand__sub  { font-size: 17px; letter-spacing: 3px; margin-top: 6px; }

  .connectors { position: absolute; inset: 0; }

  .name-box {
    position: absolute; left: 150px; top: 188px; width: 245px; height: 66px;
    background: var(--line-white); color: var(--ink-dark);
    text-align: center; padding-top: 10px;
  }
  .name-box__name  { font-size: 22px; font-weight: 700; letter-spacing: 1px; }
  .name-box__title { font-size: 13px; margin-top: 2px; }

  .contact-box {
    position: absolute; left: 110px; width: 285px; height: 80px;
    border: 2px solid var(--line-white); color: var(--line-white);
    text-align: center; padding-top: 13px;
  }
  .contact-box--phone   { top: 290px; }
  .contact-box--email   { top: 400px; }
  .contact-box--website { top: 510px; }
  .contact-box__label { font-size: 19px; font-weight: 700; letter-spacing: 1px; }
  .contact-box__value { font-size: 14px; margin-top: 6px; letter-spacing: .5px; }

  .address-band {
    position: absolute; left: 0; right: 0; bottom: 0; height: 95px;
    background: var(--accent-yellow); color: var(--ink-dark);
    display: flex; align-items: center; padding-left: 22px;
    font-size: 17px; font-weight: 500; letter-spacing: .5px;
  }

  /* Back */
  .back-edge { position: absolute; left: 0; right: 0; top: 398px; height: 6px; background: var(--edge-blue); }
  .back-panel {
    position: absolute; left: 0; right: 0; top: 404px; bottom: 0;
    background: var(--accent-yellow); color: var(--ink-dark);
    padding: 90px 0 0 40px;
    font-size: 20px; font-weight: 500; line-height: 1.6; letter-spacing: .5px;
  }
</style>
</head>
<body>
<main class="canvas">

  <section class="card card--front" aria-label="Business card front">
    <div class="top-rule top-rule--thin"></div>
    <div class="top-rule top-rule--thick"></div>

    <div class="brand">
      <div class="brand__name">KOLVEN</div>
      <div class="brand__sub">SOLUTIONS INC.</div>
    </div>
    <div class="logo-rule"></div>

    <svg class="connectors" width="420" height="735" viewBox="0 0 420 735" aria-hidden="true">
      <g stroke="#ffffff" stroke-width="2" fill="none">
        <line x1="40" y1="221" x2="40" y2="550"/>
        <line x1="40" y1="221" x2="150" y2="221"/>
        <line x1="40" y1="330" x2="110" y2="330"/>
        <line x1="40" y1="440" x2="110" y2="440"/>
        <line x1="40" y1="550" x2="110" y2="550"/>
      </g>
    </svg>

    <div class="name-box">
      <div class="name-box__name">DEREK NAMSBY</div>
      <div class="name-box__title">Sales Manager</div>
    </div>

    <div class="contact-box contact-box--phone">
      <div class="contact-box__label">PHONE</div>
      <div class="contact-box__value">905-481-2976 · Fax 905-481-2976</div>
    </div>
    <div class="contact-box contact-box--email">
      <div class="contact-box__label">EMAIL</div>
      <div class="contact-box__value">derek@kolvensolutions-example.com</div>
    </div>
    <div class="contact-box contact-box--website">
      <div class="contact-box__label">WEBSITE</div>
      <div class="contact-box__value">www.kolvensolutions-example.com</div>
    </div>

    <div class="address-band">14 Pinemarsh Lane, Brampton L7P 2K9</div>
  </section>

  <section class="card card--back" aria-label="Business card back">
    <div class="back-edge"></div>
    <div class="back-panel">
      14 Pinemarsh Lane,<br>Brampton L7P 2K9
    </div>
  </section>

</main>
</body>
</html>
```